business card deign

Logo needs the following on it.
1. attached logo
2. Tagline - "From chilled cans to late nights...we bring the good times!"
3. Name- Dalton Pikes, Founder and CPO
4. Address - 412 E. Carver Avenue, Ste 2207, Larkmoor, NC. 33917
5. Phone - 555.318.4726

```html
<!DOCTYPE html>
<html lang="en">
<head>
<meta charset="utf-8">
<title>Kelvra Business Card</title>
<link href="https://fonts.googleapis.com/css2?family=Montserrat:wght@400;500;700;800&display=swap" rel="stylesheet">
<style>
  :root {
    --stage: #3a3a3a;
    --card-black: #0d0d0d;
    --card-white: #ffffff;
    --ink: #111111;
    --paper-ink: #f4f4f4;
  }
  * { margin: 0; padding: 0; box-sizing: border-box; }
  html, body {
    width: 1200px; height: 689px; overflow: hidden;
    background: var(--stage);
    font-family: "Montserrat", sans-serif;
  }
  .stage {
    position: relative; width: 1200px; height: 689px;
    display: flex; align-items: center; justify-content: center; gap: 40px;
  }
  .card {
    position: relative; width: 540px; height: 309px;
    border-radius: 22px; overflow: hidden;
    box-shadow: 0 18px 40px rgba(0,0,0,.45);
  }
  /* Back */
  .card-back { background: var(--card-black); }
  .back-pattern {
    position: absolute; inset: 0;
    background:
      linear-gradient(110deg, rgba(220,220,220,.55) 0%, rgba(140,140,140,.25) 35%, rgba(30,30,30,.15) 60%, rgba(0,0,0,0) 100%),
      var(--card-black);
  }
  .back-brand {
    position: absolute; left: 50%; top: 50%;
    transform: translate(-50%, -50%);
    display: flex; align-items: center; gap: 14px;
    color: var(--paper-ink);
    font-weight: 800; font-size: 40px; letter-spacing: 12px;
  }
  .brand-dot {
    width: 22px; height: 22px; border-radius: 50%;
    background: currentColor; flex: none;
  }
  /* Front */
  .card-front { background: var(--card-white); color: var(--ink); }
  .front-brand {
    position: absolute; left: 34px; top: 112px; width: 200px;
    display: flex; flex-direction: column; align-items: center; gap: 12px;
    font-weight: 800; font-size: 26px; letter-spacing: 9px;
  }
  .front-brand .brand-dot { width: 34px; height: 34px; }
  .divider {
    position: absolute; left: 262px; top: 60px;
    width: 2px; height: 130px; background: var(--ink);
  }
  .contact { position: absolute; left: 284px; top: 52px; }
  .person-name { font-weight: 800; font-size: 19px; letter-spacing: .5px; }
  .person-role { font-size: 15px; margin-top: 2px; }
  .contact-list { list-style: none; margin-top: 22px; font-size: 14.5px; line-height: 1.35; }
  .contact-list li { display: flex; gap: 8px; align-items: flex-start; margin-bottom: 4px; }
  .contact-list svg { flex: none; margin-top: 2px; }
  .tagline {
    position: absolute; left: 0; right: 0; bottom: 42px;
    text-align: center; font-size: 15.5px; font-weight: 500;
  }
</style>
</head>
<body>
<main class="stage">
  <section class="card card-back">
    <div class="back-pattern" role="img" aria-label="Repeating brand pattern fading from silver to black"></div>
    <div class="back-brand"><span class="brand-dot"></span>KELVRA</div>
  </section>

  <section class="card card-front">
    <div class="front-brand"><span class="brand-dot"></span>KELVRA</div>
    <div class="divider"></div>
    <div class="contact">
      <p class="person-name">DALTON PIKES</p>
      <p class="person-role">Founder and CPO</p>
      <ul class="contact-list">
        <li>
          <svg width="14" height="14" viewBox="0 0 24 24"><path fill="#111" d="M6.6 10.8a15.1 15.1 0 0 0 6.6 6.6l2.2-2.2a1 1 0 0 1 1-.25 11.4 11.4 0 0 0 3.6.57 1 1 0 0 1 1 1V20a1 1 0 0 1-1 1A17 17 0 0 1 3 4a1 1 0 0 1 1-1h3.5a1 1 0 0 1 1 1c0 1.25.2 2.45.57 3.57a1 1 0 0 1-.25 1z"/></svg>
          <span>555.318.4726</span>
        </li>
        <li>
          <svg width="14" height="16" viewBox="0 0 24 28"><path fill="#111" d="M12 0a9 9 0 0 0-9 9c0 7 9 19 9 19s9-12 9-19a9 9 0 0 0-9-9zm0 12.5A3.5 3.5 0 1 1 12 5.5a3.5 3.5 0 0 1 0 7z"/></svg>
          <span>412 E. Carver Avenue, Ste<br>2207, Larkmoor, NC. 33917</span>
        </li>
      </ul>
    </div>
    <p class="tagline">From chilled cans to late nights...we bring the good times!</p>
  </section>
</main>
</body>
</html>
```